New Business Card Design Project LORVANTI-Italy

we are LORVANTI-Italy
our company in the market for 3 years we are luxury cosmetic company and its about time for a facelift :)
i will like to have elegant luxurious and unique business card
that will give the person that get it a unique, luxurious and elegant impression
I'm VERY OPEN FOR NEW IDEAS , even duo i add a few files of things that i see on line and i like them

i add my logo as well
my website is LORVANTI.COM
(if you would like to see the main style that we have)

Target Market(s)

adult that have money :)

Industry/Entity Type

Business

Contact Information for Business Card

Name - Dario Lorvanti
Position - CEO and CO Founder
address - 4817 E Halvern
telephone - 555-384-1926
email - dario@lorvanti.com
fax - 555-384-1926
website - LORVANTI.COM

Colors
000000
959595
fbee3e
ffffff

Requirements
Must have
• big logo in GOLD color
• elegant look
• impressive
Nice to have
• not must but maybe classy pattern background
• not must but maybe emblem
• maybe clear plastic business card
Should not have
• colors
• images

```html
<!DOCTYPE html>
<html lang="en">
<head>
<meta charset="utf-8">
<title>LORVANTI Italy – Business Card</title>
<link rel="stylesheet" href="https://fonts.googleapis.com/css2?family=Roboto:wght@400;500;700&display=swap">
<style>
  :root {
    --stage: #262626;
    --card: #141414;
    --card-inner: #1c1c1c;
    --gold: #e4bd3c;
    --gold-light: #fbee3e;
    --gold-deep: #b8891c;
    --white: #ffffff;
    --grey: #959595;
  }
  * { margin: 0; padding: 0; box-sizing: border-box; }
  html, body {
    width: 1200px;
    height: 900px;
    overflow: hidden;
    background: var(--stage);
    font-family: "Roboto", Arial, sans-serif;
  }
  .stage {
    width: 1200px;
    height: 900px;
    display: flex;
    flex-direction: column;
    align-items: center;
    justify-content: center;
    gap: 44px;
  }
  .card {
    width: 580px;
    height: 332px;
    background: var(--card);
    position: relative;
    box-shadow: 0 10px 28px rgba(0,0,0,0.55);
  }

  /* Front */
  .card-front {
    display: flex;
    flex-direction: column;
    align-items: center;
    justify-content: center;
    gap: 22px;
  }
  .brand-mark {
    width: 72px;
    height: 72px;
    border: 2px solid var(--gold);
    border-radius: 50%;
  }
  .brand-name {
    color: var(--gold);
    font-weight: 500;
    font-size: 34px;
    letter-spacing: 6px;
    text-align: center;
    line-height: 1.1;
  }

  /* Back */
  .card-back { padding: 0; }
  .lattice-border {
    position: absolute;
    inset: 0;
    background: linear-gradient(135deg, var(--gold-deep), var(--gold-light) 45%, var(--gold) 70%, var(--gold-deep));
  }
  .back-panel {
    position: absolute;
    inset: 30px;
    background: var(--card-inner);
    outline: 2px solid var(--card);
    outline-offset: -6px;
    display: flex;
    flex-direction: column;
    align-items: center;
    justify-content: center;
    text-align: center;
    color: var(--white);
  }
  .person-name {
    color: var(--gold);
    font-weight: 700;
    font-size: 22px;
    letter-spacing: 0.5px;
  }
  .person-title {
    font-size: 14px;
    margin-top: 2px;
  }
  .divider {
    width: 26px;
    height: 1px;
    background: var(--gold);
    margin: 10px 0;
  }
  .address { font-size: 14px; }
  .contact-line {
    font-size: 14px;
    line-height: 1.55;
  }
  .contact-label { color: var(--gold); font-weight: 700; }
  .website {
    color: var(--gold);
    font-size: 14px;
    letter-spacing: 0.5px;
    margin-top: 16px;
  }
</style>
</head>
<body>
  <main class="stage">
    <section class="card card-front" aria-label="Business card front">
      <div class="brand-mark"></div>
      <div class="brand-name">LORVANTI ITALY</div>
    </section>

    <section class="card card-back" aria-label="Business card back">
      <div class="lattice-border" role="img" aria-label="Gold lattice pattern border"></div>
      <div class="back-panel">
        <div class="person-name">DARIO LORVANTI</div>
        <div class="person-title">CEO &amp; CO Founder</div>
        <div class="divider"></div>
        <div class="address">4817 E Halvern</div>
        <div class="divider"></div>
        <div class="contact-line">
          <span class="contact-label">P:</span> 555-384-1926
          <span class="contact-label">F:</span> 555-384-1926
        </div>
        <div class="contact-line">
          <span class="contact-label">E:</span> dario@lorvanti.com
        </div>
        <div class="website">WWW.LORVANTI.COM</div>
      </div>
    </section>
  </main>
</body>
</html>
```